Car wash line needed for the pylon inscription

We need a design template / print template for our advertising pylon so that the Korvane plates can be printed. The area to be printed is approx. 1.5m wide and approx. 2.70m high. We operate a car wash about 30m long. The washing rollers are equipped with scratch-free Velmo Tex foam material. Before the vehicle is put into the car wash it gets a manual high pressure pre-wash. There are four different washing programs: basic laundry € 7.50 (wheel cleaning, intensive washing, gloss drying comfort care € 10.50 (like base + active foam) special care € 13.00 (like comfort + glossy sealing with lotus wax) premium care € 15.50 (like special care + Underbody wash) The pylon is right on the driveway on a busy road, we want to achieve maximum attention with the pylons. It should not be too much content because the vehicles drive past it, due to an immediate gyro, the speed is however at about 40Km / h. Opening hours Mon-Fri. 08: 00-19: 00 Sat 07: 00-19: 00 The Korvane plates are red. The enclosed files show our pylon with a little appealing design proposal our advertising agency and the real local places. For the opinion you can see on the following link a youtube video with a comparable car wash like ours, the washing process is well illustrated there. https://www.clipvault-demo.net/watch?v=Qk7rTzP2mLw Furthermore, we have a bonus card system who has washed our car 10 times gets the 11 laundry for free. From foam additives we use active foam from the comfort care and from the special care gets the vehicle lotus wax, which has the effect that the paint is sealed and keeps the shine longer. We need a design template / print template for our advertising pylon so that the Korvane plates can be printed. The area to be printed is approx. 1.5m wide and approx. 2.70m high. We operate a car wash about 30m long. The washing rollers are equipped with scratch-free Velmo Tex foam material. Before the vehicle is put into the car wash it gets a manual high pressure pre-wash. There are four different washing programs: basic laundry € 7.50 (wheel cleaning, intensive washing, gloss drying comfort care € 10.50 (like base + active foam) special care € 13.00 (like comfort + glossy sealing with lotus wax) premium care € 15.50 (like special care + Underbody wash) The pylon is right on the driveway on a busy road, we want to achieve maximum attention with the pylons. It should not be too much content because the vehicles drive past it, due to an immediate gyro, the speed is however at about 40Km / h. Opening hours Mon-Fri. 08: 00-19: 00 Sat 07: 00-19: 00 The Korvane plates are red. The enclosed files show our pylon with a little appealing design proposal our advertising agency and the real local places. For the opinion you can see on the following link a youtube video with a comparable car wash like ours, the washing process is well illustrated there. https://www.clipvault-demo.net/watch?v=Qk7rTzP2mLw Furthermore, we have a bonus card system who has washed our car 10 times gets the 11 laundry for free. From foam additives we use active foam from the comfort care and from the special care gets the vehicle lotus wax, which has the effect that the paint is sealed and keeps the shine longer. We need a design template / print template for our advertising pylon so that the Korvane plates can be printed. The area to be printed is approx. 1.5m wide and approx. 2.70m high. We operate a car wash about 30m long. The washing rollers are equipped with scratch-free Velmo Tex foam material. Before the vehicle is put into the car wash it gets a manual high pressure pre-wash. There are four different washing programs: basic laundry € 7.50 (wheel cleaning, intensive washing, gloss drying comfort care € 10.50 (like base + active foam) special care € 13.00 (like comfort + glossy sealing with lotus wax) premium care € 15.50 (like special care + Underbody wash) The pylon is right on the driveway on a busy road, we want to achieve maximum attention with the pylons. It should not be too much content because the vehicles drive past it, due to an immediate gyro, the speed is however at about 40Km / h. Opening hours Mon-Fri. 08: 00-19: 00 Sat 07: 00-19: 00 The Korvane plates are red. The enclosed files show our pylon with a little appealing design proposal our advertising agency and the real local places. For the opinion you can see on the following link a youtube video with a comparable car wash like ours, the washing process is well illustrated there. https://www.clipvault-demo.net/watch?v=Qk7rTzP2mLw Furthermore, we have a bonus card system who has washed our car 10 times gets the 11 laundry for free. From foam additives we use active foam from the comfort care and from the special care gets the vehicle lotus wax, which has the effect that the paint is sealed and keeps the shine longer. We need a design template / print template for our advertising pylon so that the Korvane plates can be printed. The area to be printed is approx. 1.5m wide and approx. 2.70m high. We operate a car wash about 30m long. The washing rollers are equipped with scratch-free Velmo Tex foam material. Before the vehicle is put into the car wash it gets a manual high pressure pre-wash. There are four different washing programs: basic laundry € 7.50 (wheel cleaning, intensive washing, gloss drying comfort care € 10.50 (like base + active foam) special care € 13.00 (like comfort + glossy sealing with lotus wax) premium care € 15.50 (like special care + Underbody wash) The pylon is right on the driveway on a busy road, we want to achieve maximum attention with the pylons. It should not be too much content because the vehicles drive past it, due to an immediate gyro, the speed is however at about 40Km / h. Opening hours Mon-Fri. 08: 00-19: 00 Sat 07: 00-19: 00 The Korvane plates are red. The enclosed files show our pylon with a little appealing design proposal our advertising agency and the real local places. For the opinion you can see on the following link a youtube video with a comparable car wash like ours, the washing process is well illustrated there. https://www.clipvault-demo.net/watch?v=Qk7rTzP2mLw Furthermore, we have a bonus card system who has washed our car 10 times gets the 11 laundry for free. From foam additives we use active foam from the comfort care and from the special care gets the vehicle lotus wax, which has the effect that the paint is sealed and keeps the shine longer. We need a design template / print template for our advertising pylon so that the Korvane plates can be printed. The area to be printed is approx. 1.5m wide and approx. 2.70m high. We operate a car wash about 30m long. The washing rollers are equipped with scratch-free Velmo Tex foam material. Before the vehicle is put into the car wash it gets a manual high pressure pre-wash. There are four different washing programs: basic laundry € 7.50 (wheel cleaning, intensive washing, gloss drying comfort care € 10.50 (like base + active foam) special care € 13.00 (like comfort + glossy sealing with lotus wax) premium care € 15.50 (like special care + Underbody wash) The pylon is right on the driveway on a busy road, we want to achieve maximum attention with the pylons. It should not be too much content because the vehicles drive past it, due to an immediate gyro, the speed is however at about 40Km / h. Opening hours Mon-Fri. 08: 00-19: 00 Sat 07: 00-19: 00 The Korvane plates are red. The enclosed files show our pylon with a little appealing design proposal our advertising agency and the real local places. For the opinion you can see on the following link a youtube video with a comparable car wash like ours, the washing process is well illustrated there. https://www.clipvault-demo.net/watch?v=Qk7rTzP2mLw Furthermore, we have a bonus card system who has washed our car 10 times gets the 11 laundry for free. From foam additives we use active foam from the comfort care and from the special care gets the vehicle lotus wax, which has the effect that the paint is sealed and keeps the shine longer. We need a design template / print template for our advertising pylon so that the Korvane plates can be printed. The area to be printed is approx. 1.5m wide and approx. 2.70m high. We operate a car wash about 30m long. The washing rollers are equipped with scratch-free Velmo Tex foam material. Before the vehicle is put into the car wash it gets a manual high pressure pre-wash. There are four different washing programs: basic laundry € 7.50 (wheel cleaning, intensive washing, gloss drying comfort care € 10.50 (like base + active foam) special care € 13.00 (like comfort + glossy sealing with lotus wax) premium care € 15.50 (like special care + Underbody wash) The pylon is right on the driveway on a busy road, we want to achieve maximum attention with the pylons. It should not be too much content because the vehicles drive past it, due to an immediate gyro, the speed is however at about 40Km / h. Opening hours Mon-Fri. 08: 00-19: 00 Sat 07: 00-19: 00 The Korvane plates are red. The enclosed files show our pylon with a little appealing design proposal our advertising agency and the real local places. For the opinion you can see on the following link a youtube video with a comparable car wash like ours, the washing process is well illustrated there. https://www.clipvault-demo.net/watch?v=Qk7rTzP2mLw Furthermore, we have a bonus card system who has washed our car 10 times gets the 11 laundry for free. From foam additives we use active foam from the comfort care and from the special care gets the vehicle lotus wax, which has the effect that the paint is sealed and keeps the shine longer. We need a design template / print template for our advertising pylon so that the Korvane plates can be printed. The area to be printed is approx. 1.5m wide and approx. 2.70m high. We operate a car wash about 30m long. The washing rollers are equipped with scratch-free Velmo Tex foam material. Before the vehicle is put into the car wash it gets a manual high pressure pre-wash. There are four different washing programs: basic laundry € 7.50 (wheel cleaning, intensive washing, gloss drying comfort care € 10.50 (like base + active foam) special care € 13.00 (like comfort + glossy sealing with lotus wax) premium care € 15.50 (like special care + Underbody wash) The pylon is right on the driveway on a busy road, we want to achieve maximum attention with the pylons. It should not be too much content because the vehicles drive past it, due to an immediate gyro, the speed is however at about 40Km / h. Opening hours Mon-Fri. 08: 00-19: 00 Sat 07: 00-19: 00 The Korvane plates are red. The enclosed files show our pylon with a little appealing design proposal our advertising agency and the real local places. For the opinion you can see on the following link a youtube video with a comparable car wash like ours, the washing process is well illustrated there. https://www.clipvault-demo.net/watch?v=Qk7rTzP2mLw Furthermore, we have a bonus card system who has washed our car 10 times gets the 11 laundry for free. From foam additives we use active foam from the comfort care and from the special care gets the vehicle lotus wax, which has the effect that the paint is sealed and keeps the shine longer. We need a design template / print template for our advertising pylon so that the Korvane plates can be printed. The area to be printed is approx. 1.5m wide and approx. 2.70m high. We operate a car wash about 30m long. The washing rollers are equipped with scratch-free Velmo Tex foam material. Before the vehicle is put into the car wash it gets a manual high pressure pre-wash. There are four different washing programs: basic laundry € 7.50 (wheel cleaning, intensive washing, gloss drying comfort care € 10.50 (like base + active foam) special care € 13.00 (like comfort + glossy sealing with lotus wax) premium care € 15.50 (like special care + Underbody wash) The pylon is right on the driveway on a busy road, we want to achieve maximum attention with the pylons. It should not be too much content because the vehicles drive past it, due to an immediate gyro, the speed is however at about 40Km / h. Opening hours Mon-Fri. 08: 00-19: 00 Sat 07: 00-19: 00 The Korvane plates are red. The enclosed files show our pylon with a little appealing design proposal our advertising agency and the real local places. For the opinion you can see on the following link a youtube video with a comparable car wash like ours, the washing process is well illustrated there. https://www.clipvault-demo.net/watch?v=Qk7rTzP2mLw Furthermore, we have a bonus card system who has washed our car 10 times gets the 11 laundry for free. From foam additives we use active foam from the comfort care and from the special care gets the vehicle lotus wax, which has the effect that the paint is sealed and keeps the shine longer. We need a design template / print template for our advertising pylon so that the Korvane plates can be printed. The area to be printed is approx. 1.5m wide and approx. 2.70m high. We operate a car wash about 30m long. The washing rollers are equipped with scratch-free Velmo Tex foam material. Before the vehicle is put into the car wash it gets a manual high pressure pre-wash. There are four different washing programs: basic laundry € 7.50 (wheel cleaning, intensive washing, gloss drying comfort care € 10.50 (like base + active foam) special care € 13.00 (like comfort + glossy sealing with lotus wax) premium care € 15.50 (like special care + Underbody wash) The pylon is right on the driveway on a busy road, we want to achieve maximum attention with the pylons. It should not be too much content because the vehicles drive past it, due to an immediate gyro, the speed is however at about 40Km / h. Opening hours Mon-Fri. 08: 00-19: 00 Sat 07: 00-19: 00 The Korvane plates are red. The enclosed files show our pylon with a little appealing design proposal our advertising agency and the real local places. For the opinion you can see on the following link a youtube video with a comparable car wash like ours, the washing process is well illustrated there. https://www.clipvault-demo.net/watch?v=Qk7rTzP2mLw Furthermore, we have a bonus card system who has washed our car 10 times gets the 11 laundry for free. From foam additives we use active foam from the comfort care and from the special care gets the vehicle lotus wax, which has the effect that the paint is sealed and keeps the shine longer.

Target Market(s)

germany

Colors

Designer to choose colors to be used in the design.

Requirements
Must have
• Print template for the print job in the accepted formats. Of course, the design must be in German
Nice to have
• Colors that attract attention, but are still serious. The content must be perceived when passing by and the customers must be aware of the car wash.
Should not have
• Kitschiges Design Too much content which takes longer to be read.

```html
<!DOCTYPE html>
<html lang="de">
<head>
<meta charset="utf-8">
<title>Waschstrasse am Talring – Pylon</title>
<link rel="stylesheet" href="https://fonts.googleapis.com/css2?family=Archivo+Black&family=Oswald:wght@500;700&display=swap">
<style>
  :root {
    --page: #f4f4f4;
    --sheet: #ffffff;
    --signal-red: #d10000;
    --plate-grey: #7a7a7a;
    --post: #32333c;
    --panel-purple: #5a045a;
    --label-yellow: #ffe100;
    --label-red: #e8202a;
    --price-green: #008c45;
    --price-red: #ee1d23;
    --price-plum: #9c1c63;
    --price-blue: #134a9b;
    --badge-navy: #0c3778;
    --banner-deep: #003a7f;
    --banner-light: #0a8fd0;
    --swoosh: #fbb316;
    --foam-blue: #0092dc;
    --white: #ffffff;
  }
  html, body {
    margin: 0;
    width: 800px;
    height: 1200px;
    overflow: hidden;
    background: var(--page);
  }
  .pylon-sheet { display: block; width: 800px; height: 1200px; }
  .brand-name { font-family: "Oswald", sans-serif; font-weight: 700; fill: var(--white); }
  .headline { font-family: "Archivo Black", sans-serif; fill: var(--white); }
  .badge-number { font-family: "Archivo Black", sans-serif; fill: var(--white); }
  .feature-note { font-family: "Oswald", sans-serif; font-weight: 500; fill: var(--label-yellow); }
  .program-name { font-family: "Archivo Black", sans-serif; fill: var(--label-red); }
  .program-price { font-family: "Oswald", sans-serif; font-weight: 700; fill: var(--white); }
  .program-detail { font-family: "Archivo Black", sans-serif; fill: var(--white); }
  .opening-hours { font-family: "Oswald", sans-serif; font-weight: 500; fill: var(--label-red); }
</style>
</head>
<body>
<svg class="pylon-sheet" viewBox="0 0 800 1200" xmlns="http://www.w3.org/2000/svg">
  <defs>
    <linearGradient id="banner-gradient" x1="0" y1="0" x2="1" y2="0">
      <stop offset="0" stop-color="var(--banner-deep)"/>
      <stop offset="0.55" stop-color="#00508f"/>
      <stop offset="1" stop-color="var(--banner-light)"/>
    </linearGradient>
    <clipPath id="panel-clip"><rect x="228" y="506" width="334" height="607"/></clipPath>
  </defs>

  <rect class="sheet" x="9" y="9" width="782" height="1182" fill="var(--sheet)"/>

  <!-- sign head -->
  <g class="sign-head">
    <circle cx="395" cy="234" r="189" fill="var(--white)" stroke="#555" stroke-width="0.8"/>
    <circle cx="395" cy="234" r="185" fill="var(--signal-red)"/>
    <circle cx="395" cy="234" r="151" fill="var(--white)" stroke="#555" stroke-width="0.6"/>
    <circle cx="395" cy="234" r="147" fill="var(--plate-grey)"/>
    <circle class="emblem-mark" cx="395" cy="210" r="62" fill="none" stroke="var(--foam-blue)" stroke-width="9"/>

    <path class="direction-arrow" fill="var(--signal-red)"
      d="M178,297 H615 Q641,297 641,323 V456 Q641,482 615,482 H178 V515 L102,460 L178,405 Z"/>

    <rect class="name-plate-rim" x="178" y="297" width="431" height="153" rx="17" fill="var(--white)" stroke="#555" stroke-width="0.8"/>
    <rect class="name-plate" x="184" y="303" width="420" height="141" rx="12" fill="var(--plate-grey)" stroke="#444" stroke-width="0.6"/>
    <text class="brand-name" x="396" y="389" font-size="62" text-anchor="middle" textLength="370" lengthAdjust="spacingAndGlyphs">WASCHSTRASSE</text>
    <text class="brand-name" x="396" y="430" font-size="32" text-anchor="middle" letter-spacing="1">AM TALRING</text>
  </g>

  <!-- post -->
  <rect class="pylon-post" x="197" y="482" width="400" height="655" fill="var(--post)"/>
  <rect class="panel-rim" x="223" y="502" width="344" height="616" fill="var(--white)"/>
  <rect class="price-panel" x="228" y="506" width="334" height="607" fill="var(--panel-purple)"/>

  <!-- header -->
  <g class="panel-header" clip-path="url(#panel-clip)">
    <path class="header-swoosh" fill="var(--swoosh)"
      d="M228,506 H540 V618 Q440,640 335,614 Q255,588 228,506 Z"/>
    <path class="header-banner" fill="url(#banner-gradient)"
      d="M232,506 H540 V604 Q440,622 340,598 Q262,574 232,506 Z"/>
    <circle class="feature-disc" cx="568" cy="564" r="80" fill="var(--panel-purple)" stroke="var(--white)" stroke-width="2"/>
    <text class="feature-note" text-anchor="middle" font-size="16">
      <tspan x="533" y="533">SCRATCH-</tspan>
      <tspan x="535" y="549">FREE</tspan>
      <tspan x="529" y="570">VELMO TEX</tspan>
      <tspan x="535" y="586">FOAM</tspan>
      <tspan x="534" y="602">MATERIAL</tspan>
    </text>
  </g>
  <g class="program-badge">
    <circle cx="275" cy="560" r="36" fill="var(--label-yellow)"/>
    <circle cx="275" cy="560" r="31" fill="var(--badge-navy)" stroke="var(--white)" stroke-width="2"/>
    <text class="badge-number" x="275" y="579" font-size="52" text-anchor="middle">4</text>
  </g>
  <text class="headline" font-size="25">
    <tspan x="320" y="539" textLength="155" lengthAdjust="spacingAndGlyphs">DIFFERENT</tspan>
    <tspan x="320" y="564" textLength="137" lengthAdjust="spacingAndGlyphs">WASHING</tspan>
    <tspan x="320" y="589" textLength="164" lengthAdjust="spacingAndGlyphs">PROGRAMS</tspan>
  </text>

  <!-- program rows -->
  <g class="program basic">
    <path fill="#000" d="M228,638 H408 L395,693 H228 Z"/>
    <path class="label-bar" fill="var(--label-yellow)" d="M228,636 H406 L393,689 H228 Z"/>
    <path class="price-bar" fill="var(--price-green)" d="M416,636 H562 V691 H402 Z"/>
    <text class="program-name" text-anchor="end" font-size="24"><tspan x="386" y="662">BASIC</tspan><tspan x="386" y="686">LAUNDRY</tspan></text>
    <text class="program-price" x="414" y="684" font-size="44">€ 7.50</text>
    <text class="program-detail" font-size="17"><tspan x="248" y="714">(WHEEL CLEANING,</tspan><tspan x="248" y="733">INTENSIVE WASHING,</tspan><tspan x="248" y="752">GLOSS DRYING)</tspan></text>
  </g>

  <g class="program comfort">
    <path fill="#000" d="M228,764 H408 L395,818 H228 Z"/>
    <path class="label-bar" fill="var(--label-yellow)" d="M228,762 H406 L393,814 H228 Z"/>
    <path class="price-bar" fill="var(--price-red)" d="M416,762 H562 V816 H402 Z"/>
    <text class="program-name" text-anchor="end" font-size="24"><tspan x="386" y="788">COMFORT</tspan><tspan x="386" y="811">CARE</tspan></text>
    <text class="program-price" x="414" y="810" font-size="44">€ 10.50</text>
    <text class="program-detail" x="247" y="840" font-size="17">(LIKE BASE +ACTIVE FOAM)</text>
  </g>

  <g class="program special">
    <path fill="#000" d="M228,853 H408 L395,906 H228 Z"/>
    <path class="label-bar" fill="var(--label-yellow)" d="M228,851 H406 L393,902 H228 Z"/>
    <path class="price-bar" fill="var(--price-plum)" d="M416,851 H562 V904 H402 Z"/>
    <text class="program-name" text-anchor="end" font-size="24"><tspan x="383" y="877">SPECIAL</tspan><tspan x="383" y="900">CARE</tspan></text>
    <text class="program-price" x="414" y="897" font-size="44">€ 13.00</text>
    <text class="program-detail" font-size="17"><tspan x="246" y="931">(LIKE COMFORT +</tspan><tspan x="246" y="950">GLOSSY SEALING WITH</tspan><tspan x="246" y="969">LOTUS WAX)</tspan></text>
  </g>

  <g class="program premium">
    <path fill="#000" d="M228,977 H408 L395,1031 H228 Z"/>
    <path class="label-bar" fill="var(--label-yellow)" d="M228,975 H406 L393,1027 H228 Z"/>
    <path class="price-bar" fill="var(--price-blue)" d="M416,975 H562 V1029 H402 Z"/>
    <text class="program-name" text-anchor="end" font-size="24"><tspan x="386" y="1001">PREMIUM</tspan><tspan x="386" y="1024">CARE</tspan></text>
    <text class="program-price" x="414" y="1021" font-size="44">€ 15.50</text>
    <text class="program-detail" font-size="17"><tspan x="247" y="1053">(LIKE SPECIAL CARE +</tspan><tspan x="247" y="1073">UNTERBODENWÄSCHE)</tspan></text>
  </g>

  <!-- footer -->
  <path class="hours-band" fill="var(--label-yellow)" d="M228,1082 Q395,1100 562,1082 V1113 H228 Z"/>
  <text class="opening-hours" x="395" y="1109" font-size="16" text-anchor="middle" textLength="296" lengthAdjust="spacingAndGlyphs">MON-FRI. 08: 00-19: 00 SAT 07: 00-19: 00</text>
</svg>
</body>
</html>
```